Equipment Finance Specialist I work with companies who need the funds to buy their equipment

I would like a business card that stands out on the shelves. I want to be able to hand it to someone and say WOW. This card should have my logo.
You can put color into it I am very open on design and color

What my company does is we deal with dealerships that sell equipment such as Dump Trucks garbage trucks tractors trailers. Customers get referred to us and depending on their time in business we will ask for the following items

Companies that have been in business for more than two years we have a credit application program up to 250K . With this program we need the following items Credit application filled out(which is what I would like to be able for the customer to click on my website to get.) as well as three current month bank statements.

Deals over 250k we will need the following items

2 years business tax returns
2 years personal tax returns
Profit & Loss statement
Personal Financial Statement

what we do
100% FINANCING
SEASONAL PAYMENTS
LOAN BALLOON PAYMENTS
TRAC LEASING
LOW-INTEREST REFINANCING RATES
DEBT CONSOLIDATION

We specialize in creative financing solutions and offer a variety of reliable, flexible and expandable lending choices.

Target Market(s)

Trucking Companies

Industry/Entity Type

Trucking Company

Contact Information for Business Card

* $250,000 Application only Program
* Loans from $30,000 to 5,000,000
* Competitive Interest Rates

Font styles to use
Serif
Sans Serif

Colors

Designer to choose colors to be used in the design.

Requirements
Must have
• On the back of the card.
• * $250,000 Application only Program
• * Loans from $30,000 to 5,000,000
• My name, email, website. address
• * Competitive Interest Rates
• * 100% Financing
Nice to have
• I want my logo to pop on the card
• My logo is the great one I would like to use
Should not have
• I am up for your creativity as well

```html
<!DOCTYPE html>
<html lang="en">
<head>
<meta charset="utf-8">
<title>Summit Lending – Business Card</title>
<link rel="stylesheet" href="https://fonts.googleapis.com/css2?family=Montserrat:wght@800&family=Work+Sans:wght@400;500&display=swap">
<style>
  :root {
    --page-bg: #e9ecf1;
    --card-base: #f4f6f9;
    --brand-red: #d21f2b;
    --brand-red-deep: #b5121d;
    --brand-navy: #1c2150;
    --navy-soft: #3a4173;
    --name-tint: #e4e3f6;
    --detail-tint: #f1dfe4;
  }
  * { margin: 0; padding: 0; box-sizing: border-box; }
  html, body {
    width: 1200px; height: 900px; overflow: hidden;
    background: var(--page-bg);
  }
  .canvas { position: relative; width: 1200px; height: 900px; }
  .business-card {
    position: absolute; left: 150px; top: 193px;
    width: 900px; height: 514px;
    background: var(--card-base);
    overflow: hidden;
    box-shadow: 0 14px 40px rgba(20, 25, 60, 0.18);
  }
  .card-art { position: absolute; inset: 0; }
  .brand-name {
    position: absolute; right: 70px; top: 72px;
    text-align: right;
    font-family: "Montserrat", sans-serif; font-weight: 800;
    color: #ffffff; line-height: 0.95;
  }
  .brand-name .line-1 { display: block; font-size: 62px; letter-spacing: 1px; }
  .brand-name .line-2 { display: block; font-size: 33px; letter-spacing: 1px; }
  .contact-block {
    position: absolute; right: 46px; top: 232px;
    text-align: right;
    font-family: "Work Sans", sans-serif;
  }
  .person-name { font-size: 29px; font-weight: 500; letter-spacing: 1px; color: var(--name-tint); }
  .person-role { font-size: 20px; color: var(--name-tint); margin-top: 4px; margin-right: 24px; }
  .address { margin-top: 26px; margin-right: 24px; font-size: 20px; line-height: 30px; color: var(--detail-tint); letter-spacing: 0.5px; }
  .contact-lines { margin-top: 20px; list-style: none; }
  .contact-lines li {
    display: flex; justify-content: flex-end; align-items: center; gap: 10px;
    font-size: 20px; line-height: 30px; color: var(--detail-tint); letter-spacing: 0.5px;
  }
  .contact-lines svg { width: 14px; height: 14px; fill: none; stroke: var(--detail-tint); stroke-width: 1.6; }
</style>
</head>
<body>
<main class="canvas">
  <section class="business-card">
    <svg class="card-art" viewBox="0 0 900 514" width="900" height="514">
      <defs>
        <linearGradient id="redPanel" x1="0" y1="0" x2="1" y2="1">
          <stop offset="0" stop-color="var(--brand-red)"/>
          <stop offset="1" stop-color="var(--brand-red-deep)"/>
        </linearGradient>
        <radialGradient id="emblemFill" cx="0.5" cy="0.5" r="0.6">
          <stop offset="0" stop-color="var(--navy-soft)"/>
          <stop offset="1" stop-color="var(--brand-navy)"/>
        </radialGradient>
      </defs>
      <rect class="red-panel" x="432" y="0" width="468" height="514" fill="url(#redPanel)"/>
      <circle class="emblem-area" cx="302" cy="257" r="250" fill="url(#emblemFill)"
              role="img" aria-label="Dump truck emblem illustration inside a circular swoosh"/>
    </svg>

    <h1 class="brand-name"><span class="line-1">SUMMIT</span><span class="line-2">LENDING</span></h1>

    <div class="contact-block">
      <p class="person-name">DANIEL REYES</p>
      <p class="person-role">Director</p>
      <p class="address">1580 Harlow Ave.<br>Frisco, TX 75034</p>
      <ul class="contact-lines">
        <li>1300 642 917
          <svg viewBox="0 0 16 16"><path d="M4 1.5l2.5 3-1.5 1.5c.8 2 2.5 3.7 4.5 4.5l1.5-1.5 3 2.5-1.5 2.5C7 14 2 9 1.5 3z"/></svg></li>
        <li>info@summitlending.com
          <svg viewBox="0 0 16 16"><rect x="1.5" y="3.5" width="13" height="9"/><path d="M1.5 3.5l6.5 5 6.5-5"/></svg></li>
        <li>www.summitlending.com
          <svg viewBox="0 0 16 16"><circle cx="8" cy="8" r="6.5"/><ellipse cx="8" cy="8" rx="2.8" ry="6.5"/><path d="M1.5 8h13"/></svg></li>
      </ul>
    </div>
  </section>
</main>
</body>
</html>
```